Brisk Coatings business card for residential and commercial painting

A clean, professional design. Easy to read
Eye catching and elegant
Front could have some color variations
On the back of card I would like all black with signature logo

*Attached is my current business card and the items I want displayed

Contact Information for Business Card

Email, phone number, website, and owner name

Font styles to use
Serif

Requirements
Must have
• My logo with cool design and perhaps some paint splatter

```html
<!DOCTYPE html>
<html lang="en">
<head>
<meta charset="utf-8">
<title>Brisk Coatings – Business Card</title>
<link href="https://fonts.googleapis.com/css2?family=Roboto:wght@400;500;700&display=swap" rel="stylesheet">
<style>
  :root {
    --backdrop: #6b6868;
    --card-dark: #333335;
    --logo-deep: #1c1c1e;
    --paper: #f4f4f4;
    --rule: #b9b9b9;
    --brand-blue: #1470c4;
    --white: #ffffff;
  }
  * { margin: 0; padding: 0; box-sizing: border-box; }
  html, body {
    width: 1200px; height: 1200px; overflow: hidden;
    background: var(--backdrop);
    font-family: "Roboto", Arial, sans-serif;
  }
  .card {
    position: absolute;
    width: 594px; height: 350px;
    border-radius: 20px;
    overflow: hidden;
    background: var(--card-dark);
  }
  /* Back side */
  .card--back { left: 298px; top: 198px; }
  .card--back .brand-name {
    position: absolute; left: 0; right: 0; top: 80px;
    text-align: center;
    font-weight: 700; font-size: 50px; letter-spacing: 1px;
    color: var(--logo-deep);
  }
  .notes-strip {
    position: absolute; left: 0; right: 0; top: 210px; bottom: 0;
    background: var(--paper);
  }
  .notes-strip .rule {
    position: absolute; left: 35px; right: 35px;
    height: 2px; background: var(--rule);
  }
  .rule--1 { top: 35px; } .rule--2 { top: 70px; } .rule--3 { top: 105px; }

  /* Front side */
  .card--front { left: 292px; top: 636px; height: 349px; width: 593px; }
  .card--front .wave { position: absolute; inset: 0; }
  .card--front .brand-name {
    position: absolute; left: 42px; top: 70px;
    font-weight: 700; font-size: 44px; letter-spacing: 1px;
    color: var(--white);
  }
  .owner { position: absolute; left: 42px; top: 189px; }
  .owner__name { font-weight: 500; font-size: 22px; color: var(--brand-blue); line-height: 1; }
  .owner__title { margin-top: 8px; font-size: 16px; color: var(--white); }
  .contact {
    position: absolute; right: 42px; top: 248px;
    list-style: none; color: var(--white); font-size: 16px;
  }
  .contact li {
    display: flex; justify-content: flex-end; align-items: center;
    gap: 12px; height: 21.5px;
  }
  .contact svg { width: 15px; height: 15px; fill: var(--white); }
</style>
</head>
<body>

<section class="card card--back" aria-label="Card back">
  <div class="brand-name">BRISK COATINGS</div>
  <div class="notes-strip">
    <span class="rule rule--1"></span>
    <span class="rule rule--2"></span>
    <span class="rule rule--3"></span>
  </div>
</section>

<section class="card card--front" aria-label="Card front">
  <svg class="wave" viewBox="0 0 593 349" preserveAspectRatio="none" aria-hidden="true">
    <path d="M0,300 C150,335 250,300 350,242 C430,196 520,188 593,204 L593,349 L0,349 Z" fill="#1470c4"/>
    <path d="M0,262 C80,300 200,312 300,266 C400,216 480,168 593,180 L593,192 C490,184 420,226 330,268 C230,314 110,322 0,292 Z" fill="#ffffff"/>
    <path d="M45,278 C120,300 230,300 300,283 C240,300 130,302 45,278 Z" fill="#ffffff"/>
  </svg>

  <div class="brand-name">BRISK COATINGS</div>

  <div class="owner">
    <div class="owner__name">Marco "MJ"</div>
    <div class="owner__title">Owner - Licensed &amp; Insured</div>
  </div>

  <ul class="contact">
    <li>931-555-0147
      <svg viewBox="0 0 16 16" aria-hidden="true"><path d="M2 6c0-2 3-3 6-3s6 1 6 3v1h-3V6H5v1H2zM4 8h8l2 5H2z"/></svg>
    </li>
    <li>briskcoatingstn.com
      <svg viewBox="0 0 16 16" aria-hidden="true"><path d="M8 1a7 7 0 100 14A7 7 0 008 1zm0 1.5c.8 0 1.7 1.5 2 4H6c.3-2.5 1.2-4 2-4zM2.6 6.5a5.6 5.6 0 012.6-3.3c-.5 1-.8 2-.9 3.3zm0 3h1.7c.1 1.3.4 2.4.9 3.3a5.6 5.6 0 01-2.6-3.3zM6 9.5h4c-.3 2.5-1.2 4-2 4s-1.7-1.5-2-4zm4.8 3.3c.5-1 .8-2 .9-3.3h1.7a5.6 5.6 0 01-2.6 3.3zm.9-6.3c-.1-1.3-.4-2.4-.9-3.3a5.6 5.6 0 012.6 3.3zM6 8c0-.2 0-.3 0 0z"/></svg>
    </li>
    <li>hello@briskcoatingstn.com
      <svg viewBox="0 0 16 16" aria-hidden="true"><path d="M1 3h14v10H1zm1.5 1.5v.3L8 8.7l5.5-3.9v-.3zm0 2.1v4.9h11V6.6L8 10.5z"/></svg>
    </li>
  </ul>
</section>

</body>
</html>
```